MEDICAL CLINIC LETTERHEAD

Design is a letterhead for a non-profit medical center. The name of the clinic is VITARIDGE Community Health Center. Although the full name must be included, the community health center part is more of a description and should be less visible - i attached an example of what I mean by that (ATTACHED IMAGE IS AN EXAMPLE OF FONT SIZES NOT A DESIGN IDEA). Please design something modern, cool looking and unique because I can always download free templates.
Phone, email, website and etc will be added later.

Industry/Entity Type

MEDICAL

```html
<!DOCTYPE html>
<html lang="en">
<head>
<meta charset="utf-8">
<title>VITARIDGE Community Health Center – Letterhead</title>
<link href="https://fonts.googleapis.com/css2?family=Lato:wght@400;700&family=Montserrat:wght@400&family=Parisienne&display=swap" rel="stylesheet">
<style>
  :root {
    --navy: #1b2a4e;
    --gold: #a88f55;
    --ink: #3a3a3a;
    --contact-ink: #1c1c1c;
    --backdrop: #e3e3e3;
    --paper: #f6f6f6;
  }
  * { box-sizing: border-box; margin: 0; padding: 0; }
  html, body {
    width: 1153px; height: 1200px; overflow: hidden;
    background: var(--backdrop);
  }
  .letterhead {
    position: absolute; left: 169px; top: 30px;
    width: 815px; height: 1140px;
    background: radial-gradient(ellipse at 55% 32%, #ffffff 0%, var(--paper) 70%, #efefef 100%);
    box-shadow: 0 6px 18px rgba(0,0,0,0.18);
    font-family: "Lato", sans-serif;
    color: var(--ink);
    overflow: hidden;
  }
  .brand-name {
    position: absolute; left: 57px; top: 78px;
    font-family: "Lato", sans-serif; font-weight: 700;
    font-size: 44px; letter-spacing: 1px;
    color: var(--navy);
  }
  .contact {
    position: absolute; left: 557px; top: 47px;
    height: 92px; padding-left: 13px;
    border-left: 1.5px solid var(--gold);
    font-family: "Montserrat", sans-serif; font-size: 13.5px;
    color: var(--contact-ink);
  }
  .contact-name { line-height: 17.5px; margin-top: 2px; }
  .contact-list { list-style: none; margin-top: 6px; }
  .contact-list li {
    display: flex; align-items: center; height: 19.5px;
  }
  .contact-list svg { width: 12px; height: 12px; margin-right: 12px; fill: var(--gold); }
  .letter-body {
    position: absolute; left: 63px; top: 252px; width: 690px;
    font-size: 15px; line-height: 18.5px;
  }
  .date { margin-bottom: 20px; font-size: 16px; }
  .recipient, .address { font-size: 15.5px; margin-bottom: 19px; }
  .salutation { font-size: 18.5px; font-weight: 700; margin: 14px 0 18px; }
  .letter-body p.text {
    text-align: justify; line-height: 17.5px; margin-bottom: 17px;
  }
  .closing { margin-top: 38px; font-size: 15px; }
  .signature {
    font-family: "Parisienne", cursive; font-size: 36px;
    color: #222; margin-top: 18px; margin-left: 3px;
  }
  .footer-bands { position: absolute; left: 0; bottom: 0; width: 815px; height: 54px; }
</style>
</head>
<body>
  <main class="letterhead">
    <header>
      <div class="brand-name">VITARIDGE</div>
      <address class="contact">
        <div class="contact-name">VITARIDGE Community<br>Health Center</div>
        <ul class="contact-list">
          <li><svg viewBox="0 0 12 12" aria-hidden="true"><path d="M1 4c0-2 2-3 5-3s5 1 5 3v1H8V4H4v1H1zM3 6h6l2 5H1z"/></svg>987-555-0142</li>
          <li><svg viewBox="0 0 12 12" aria-hidden="true"><path d="M0 2h12v1L6 7 0 3zM0 4.5l6 4 6-4V10H0z"/></svg>hello@vitaridge-mail.com</li>
          <li><svg viewBox="0 0 12 12" aria-hidden="true"><circle cx="6" cy="6" r="5.5"/></svg>www.vitaridge-web.com</li>
        </ul>
      </address>
    </header>

    <section class="letter-body">
      <p class="date">Feb-03-2022</p>
      <p class="recipient">Mr, Owen Hale<br>President</p>
      <p class="address">Crestline Corporation<br>123 Street Name, Suite# 10<br>City, State, 120023</p>
      <p class="salutation">Dear Mr, Owen</p>
      <p class="text">Lorem ipsum dolor sit amet, consectetur adipisicing elit, sed do eiusmod tempor incididunt ut labore et dolore magna aliqua. Ut enim ad minim veniam, quis nostrud exercitation ullamco laboris nisi ut aliquip ex ea commodo consequat. Duis aute irure dolor in reprehenderit in voluptate velit esse cillum dolore eu fugiat nulla pariatur.</p>
      <p class="text">Lorem ipsum dolor sit amet, consectetur adipisicing elit, sed do eiusmod tempor incididunt ut labore et dolore magna aliqua. Ut enim ad minim veniam, quis nostrud exercitation ullamco laboris nisi ut aliquip ex ea commodo consequat. Duis aute irure dolor in reprehenderit in voluptate velit esse cillum dolore eu fugiat nulla pariatur.</p>
      <p class="text">Lorem ipsum dolor sit amet, consectetur adipisicing elit, sed do eiusmod tempor incididunt ut labore et dolore magna aliqua. Ut enim ad minim veniam, quis nostrud exercitation ullamco laboris nisi ut aliquip ex ea commodo consequat.</p>
      <p class="text">Excepteur sint occaecat cupidatat non proident, sunt in culpa qui officia deserunt mollit anim id est laborum. re et dolore magnam aliquam quaerat voluptatem.</p>
      <p class="closing">Regards</p>
      <p class="signature">Daniel Brooks</p>
    </section>

    <svg class="footer-bands" viewBox="0 0 815 54" aria-hidden="true">
      <polygon fill="var(--navy)" points="485,0 815,0 815,54 436,54"/>
      <polygon fill="var(--navy)" points="0,12 467,12 460,20 0,20"/>
      <polygon fill="var(--gold)" points="0,28 451,28 427,54 0,54"/>
    </svg>
  </main>
</body>
</html>
```